Australian Trucking Company Requires Professional Looking Stationary

We require a professional looking stationary design that incorporates our newly designed logo.

Our business, called "Brell Haulage Contracting", provides contracting work, transport and logistics to business in Western Australia particularly with links to the mining sector.

We are a small business looking to expand and our new logo and our new stationary will help develop our brand image in our market place.

Target Market(s)

Businesses and Corporation with links to the Mining Sector

Industry/Entity Type

Small Business

Requirements
Must have
• The letterhead must have the following details:
The new logo

Text saying: "Brell Holdings Pty Ltd (ACN 582 316 907) ATF The Brell Discretionary Trust T/AS"
"ABN 71 834 209 553"
Address "P.O Box 817 Wattlegrove WA, 6958"
Phone: 08 9352 7140
Email: brellhaul@mailbox-example.com.au

The text on the letterhead should be editable as the details are likely to change in the near future. Provision should be made for a website address all though one isn't available at the moment.

The styling, layout and font text is entirely up to the designer.

```html
<!DOCTYPE html>
<html lang="en">
<head>
<meta charset="utf-8">
<title>Brell Haulage Contracting – Business Card</title>
<link rel="stylesheet" href="https://fonts.googleapis.com/css2?family=Open+Sans:wght@400;600;700;800&display=swap">
<style>
  :root {
    --page-bg: #ecebe8;
    --card-white: #ffffff;
    --brand-red: #e31b23;
    --brand-red-deep: #b8141b;
    --brand-maroon: #a0151c;
    --swoosh-dark: #2b2b2b;
    --swoosh-light: #c9c9c9;
    --ink: #2a2a2a;
    --on-red: #ffffff;
  }
  * { box-sizing: border-box; margin: 0; padding: 0; }
  html, body {
    width: 1200px; height: 650px; overflow: hidden;
    background: var(--page-bg);
    font-family: "Open Sans", Arial, sans-serif;
  }
  .canvas { position: relative; width: 1200px; height: 650px; }
  .card {
    position: absolute; top: 175px;
    width: 520px; height: 300px;
    border-radius: 22px; overflow: hidden;
    box-shadow: 0 6px 18px rgba(0,0,0,0.18);
  }
  .card-front { left: 55px; background: var(--card-white); }
  .card-back {
    left: 625px;
    background: radial-gradient(ellipse at 50% 35%, var(--brand-red) 0%, var(--brand-red) 45%, var(--brand-red-deep) 100%);
  }
  .front-shape { position: absolute; inset: 0; width: 100%; height: 100%; }

  .brand {
    position: absolute; left: 40px; top: 28px;
    display: flex; align-items: center; gap: 16px;
  }
  .brand-mark {
    width: 54px; height: 54px; border-radius: 50%;
    background: var(--brand-maroon); flex: none;
  }
  .brand-name {
    font-weight: 800; font-size: 32px; line-height: 1.0;
    color: var(--brand-maroon); text-transform: uppercase;
    letter-spacing: 0.5px;
  }
  .postal-address {
    position: absolute; left: 140px; top: 118px;
    font-size: 13px; letter-spacing: 0.6px; color: var(--ink);
    white-space: nowrap;
  }
  .person {
    position: absolute; left: 90px; top: 238px; width: 150px;
    text-align: right; color: var(--on-red);
  }
  .person-name { font-weight: 700; font-size: 15px; line-height: 1.2; }
  .person-title { font-size: 12.5px; }
  .divider {
    position: absolute; left: 252px; top: 222px;
    width: 1px; height: 62px; background: rgba(255,255,255,0.75);
  }
  .contact-list {
    position: absolute; left: 264px; top: 220px;
    list-style: none; color: var(--on-red); font-size: 11.5px;
  }
  .contact-list li {
    display: flex; align-items: center; gap: 7px; height: 21px;
    white-space: nowrap;
  }
  .contact-list svg { width: 11px; height: 11px; flex: none; }

  .back-brand {
    position: absolute; left: 0; right: 0; top: 92px;
    display: flex; align-items: center; justify-content: center; gap: 16px;
  }
  .back-brand .brand-mark { background: var(--on-red); width: 58px; height: 58px; }
  .back-brand .brand-name { color: var(--on-red); font-size: 30px; }
  .legal-line {
    position: absolute; left: 20px; right: 20px; bottom: 38px;
    text-align: center; color: var(--on-red);
    font-size: 11.5px; line-height: 1.75;
  }
</style>
</head>
<body>
<main class="canvas">

  <section class="card card-front" aria-label="Business card front">
    <svg class="front-shape" viewBox="0 0 520 300" preserveAspectRatio="none" aria-hidden="true">
      <defs>
        <linearGradient id="swoosh" x1="0" x2="1" y1="0" y2="0">
          <stop offset="0" stop-color="#2b2b2b"/>
          <stop offset="0.7" stop-color="#c9c9c9"/>
          <stop offset="1" stop-color="#ffffff"/>
        </linearGradient>
        <linearGradient id="redband" x1="0" x2="0" y1="0" y2="1">
          <stop offset="0" stop-color="#e31b23"/>
          <stop offset="1" stop-color="#b8141b"/>
        </linearGradient>
      </defs>
      <path d="M0,198 Q320,194 520,112 Q330,206 0,222 Z" fill="url(#swoosh)"/>
      <path d="M0,220 Q330,204 520,124 L520,300 L0,300 Z" fill="url(#redband)"/>
    </svg>

    <div class="brand">
      <span class="brand-mark" aria-hidden="true"></span>
      <span class="brand-name">Brell Haulage<br>Contracting</span>
    </div>

    <p class="postal-address">P.O Box 817 Wattlegrove WA, 6958</p>

    <div class="person">
      <p class="person-name">Your Name</p>
      <p class="person-title">Title</p>
    </div>
    <span class="divider" aria-hidden="true"></span>

    <ul class="contact-list">
      <li>
        <svg viewBox="0 0 12 12" aria-hidden="true"><circle cx="6" cy="6" r="5.5" fill="none" stroke="#fff"/><path d="M4 3.2l1.2 1.3-.6.8c.4.9 1 1.5 1.9 1.9l.8-.6L8.6 7.8 7.8 9C5.5 8.6 3.4 6.5 3 4.2z" fill="#fff"/></svg>
        08 9352 7140
      </li>
      <li>
        <svg viewBox="0 0 12 12" aria-hidden="true"><rect x="0.5" y="2.5" width="11" height="7" fill="#fff"/><path d="M0.5 2.8L6 6.6l5.5-3.8" fill="none" stroke="#e31b23"/></svg>
        brellhaul@mailbox-example.com.au
      </li>
      <li>
        <svg viewBox="0 0 12 12" aria-hidden="true"><circle cx="6" cy="6" r="5.3" fill="none" stroke="#fff"/><ellipse cx="6" cy="6" rx="2.3" ry="5.3" fill="none" stroke="#fff"/><path d="M0.7 6h10.6" stroke="#fff"/></svg>
        www.brellhaulage-example.com
      </li>
    </ul>
  </section>

  <section class="card card-back" aria-label="Business card back">
    <div class="back-brand">
      <span class="brand-mark" aria-hidden="true"></span>
      <span class="brand-name">Brell Haulage<br>Contracting</span>
    </div>
    <p class="legal-line">
      Brell Holdings Pty Ltd (ACN 582 316 907) ATF The Brell Discretionary Trust T/AS<br>
      ABN 71 834 209 553
    </p>
  </section>

</main>
</body>
</html>
```